Business Card for a mobile physiotherapy company

I need a layout for a business card for a mobile physiotherapy company.
Slogan is "Mobile Physiotherapy - Your Road To Recovery"
Phone number is 867-555-0142
Email VardenTherapy@postnest.ca (subject to change with website)
Website www.VardenTherapy.ca
My name and credentials: Luke Varden Luke Varden, BSc(kin), MPT, CAFCI, IMS
Information maybe included: Direct Billing, Services including Physiotherapy, IMS, acupuncture
Maybe include facebook and instagram logos
One side with the logo clean and sharp
Other side with details, try not to look too busy, keep everything concise

```html
<!DOCTYPE html>
<html lang="en">
<head>
<meta charset="utf-8">
<title>Varden Therapy – Business Card</title>
<link href="https://fonts.googleapis.com/css2?family=Crimson+Pro:wght@400;600;700&display=swap" rel="stylesheet">
<style>
  :root {
    --backdrop: #c9c9c9;
    --navy: #27476b;
    --teal: #1d5a50;
    --forest: #1a5244;
    --card-white: #f4f4f2;
    --ink: #2a3444;
    --soft-white: #eef1f3;
    --muted-white: #c9d3da;
    --social: #6f8aa6;
  }
  * { box-sizing: border-box; margin: 0; padding: 0; }
  html, body { width: 1200px; height: 576px; overflow: hidden; }
  body {
    background: var(--backdrop);
    font-family: "Crimson Pro", Georgia, serif;
    position: relative;
  }
  .card {
    position: absolute;
    top: 139px;
    width: 484px;
    height: 291px;
    border-radius: 14px;
    overflow: hidden;
    box-shadow: 0 3px 8px rgba(0,0,0,0.25);
  }

  /* Front */
  .card-front {
    left: 82px;
    background: linear-gradient(35deg, var(--teal) 0%, #234f60 45%, var(--navy) 100%);
    color: var(--soft-white);
    text-align: center;
  }
  .front-name {
    position: absolute;
    top: 110px;
    left: 0;
    width: 100%;
    font-size: 48px;
    line-height: 1;
    font-weight: 700;
    color: var(--soft-white);
  }
  .front-tagline {
    position: absolute;
    top: 178px;
    width: 100%;
    font-size: 13px;
    color: var(--muted-white);
  }
  .front-services {
    position: absolute;
    top: 258px;
    width: 100%;
    font-size: 13.5px;
    color: var(--soft-white);
    word-spacing: 1px;
  }

  /* Back */
  .card-back {
    left: 602px;
    background: var(--card-white);
    color: var(--ink);
  }
  .back-band { position: absolute; inset: 0; }
  .back-name {
    position: absolute;
    top: 34px;
    left: 24px;
    display: flex;
    align-items: center;
    gap: 10px;
    font-size: 32px;
    line-height: 1;
    font-weight: 700;
    color: var(--forest);
  }
  .back-name .mark-square {
    width: 14px; height: 14px;
    background: var(--navy);
  }
  .back-tagline {
    position: absolute;
    top: 83px;
    left: 24px;
    font-size: 13px;
    font-weight: 600;
    color: var(--navy);
  }
  .person-name {
    position: absolute;
    top: 124px;
    left: 24px;
    font-size: 24px;
    font-weight: 700;
    color: var(--navy);
    letter-spacing: 0.5px;
  }
  .person-credentials {
    position: absolute;
    top: 153px;
    left: 24px;
    font-size: 12.5px;
    color: var(--ink);
  }
  .follow {
    position: absolute;
    top: 172px;
    left: 24px;
    display: flex;
    align-items: center;
    gap: 5px;
    font-size: 14px;
    color: var(--ink);
  }
  .social-dot {
    width: 19px; height: 19px;
    border-radius: 50%;
    background: var(--social);
  }
  .follow .label { margin-right: 3px; }
  .contact-list {
    position: absolute;
    top: 210px;
    left: 24px;
    list-style: none;
    font-size: 14px;
    color: var(--ink);
  }
  .contact-list li {
    display: flex;
    align-items: center;
    gap: 13px;
    height: 18px;
  }
  .contact-list svg { width: 10px; height: 10px; fill: var(--forest); }
</style>
</head>
<body>

  <section class="card card-front" aria-label="Card front">
    <p class="front-name">Varden Therapy</p>
    <p class="front-tagline">Mobile Physiotherapy - Your Road To Recovery</p>
    <p class="front-services">Direct Billing &nbsp;|&nbsp; Services Including Physiotherapy &nbsp;|&nbsp; IMS &nbsp;|&nbsp; Acupuncture</p>
  </section>

  <section class="card card-back" aria-label="Card back">
    <svg class="back-band" viewBox="0 0 484 291" preserveAspectRatio="none" aria-hidden="true">
      <polygon points="174,291 484,291 484,0 470,0" fill="var(--navy)"/>
    </svg>

    <div class="back-name">
      <span class="mark-square"></span>
      <span>Varden Therapy</span>
    </div>
    <p class="back-tagline">Mobile Physiotherapy - Your Road To Recovery</p>

    <h1 class="person-name">LUKE VARDEN</h1>
    <p class="person-credentials">BSc(kin), MPT, CAFCI, IMS</p>
    <div class="follow">
      <span class="label">Follow us on:</span>
      <span class="social-dot"></span>
      <span class="social-dot"></span>
    </div>

    <ul class="contact-list">
      <li>
        <svg viewBox="0 0 10 10" aria-hidden="true"><path d="M1 3 Q1 1 3 1 L7 1 Q9 1 9 3 L7 4 L6 3 L4 3 L3 4 Z M2 5 L8 5 L8 9 L2 9 Z"/></svg>
        <span>867-555-0142</span>
      </li>
      <li>
        <svg viewBox="0 0 10 10" aria-hidden="true"><path d="M0 2 L10 2 L10 8 L0 8 Z M1 3 L5 6 L9 3 Z" fill-rule="evenodd"/></svg>
        <span>VardenTherapy@postnest.ca</span>
      </li>
      <li>
        <svg viewBox="0 0 10 10" aria-hidden="true"><circle cx="5" cy="5" r="4.5"/><path d="M0.5 5 L9.5 5 M5 0.5 L5 9.5" stroke="var(--card-white)" stroke-width="0.8"/></svg>
        <span>www.VardenTherapy.ca</span>
      </li>
    </ul>
  </section>

</body>
</html>
```